all natural handmade soap company looking for unique stand out packaging design for bar soaps

we are looking for a unique and stand out on the shelf package design for our hand made soaps for grocery stores. we have a package soap box (picture included) but we are looking for a TOP-NOTCH, CUSTOM, STAND OUT DESIGN FOR THEM. I am supplying our current packaging design, but we want something more unique and STAND OUT. PICTURES i AM INCLUDING ARE: 1: OUR CURRENT PACKAGE DESIGN
2: OUR LIQUID SOAP LABELS (WHICH WE LOVE) AND WOULD LIKE THE BAR SOAPS TO BE SIMILAR
3: WILL BE IN A WHITE BOX WITH A LARGE CUT OUT IN FRONT (SEE SAMPLE BOX BROWN KRAFT).

Target Market(s)

VARIOUS CUSTOMERS. We sell to bright lantern grocers and various grocery stores

Industry/Entity Type

It Company

Requirements
Must have
• cool, unique look that will stand out from a store shelf
• full color acceptable
• our logo on the round part of the package (front)
• please leave a space for bar codes (usually on bottom of box)
• there is a cut out (front) that is there for people to see, feel and smell the soap
• be creative think outside the box open to fresh new designs
Nice to have
• metallic crescent moon (our logo)
Should not have
• organic cannot appear on the front

```html
<!DOCTYPE html>
<html lang="en">
<head>
<meta charset="utf-8">
<title>Wrenfield Bar Soap Packaging</title>
<link rel="stylesheet" href="https://fonts.googleapis.com/css2?family=Cinzel:wght@400&family=Comfortaa:wght@400&family=Lato:wght@400&display=swap">
<style>
  :root {
    --bg-light: #c9c9c8;
    --bg-dark: #8a8174;
    --box-white: #ffffff;
    --ink: #2a2a2a;
    --soap-olive: #8c8469;
    --soap-olive-light: #a39a7d;
    --soap-peach: #d9b48a;
    --soap-peach-light: #e6c9a3;
    --bergamot: #a8e000;
    --bergamot-fruit: #5a9a2e;
    --lemon: #f5be00;
    --lemon-fruit: #f4cf3a;
    --grapefruit: #f26b50;
    --grapefruit-fruit: #ef8a6e;
  }
  * { box-sizing: border-box; margin: 0; padding: 0; }
  html, body { width: 1200px; height: 891px; overflow: hidden; }
  body {
    background: radial-gradient(ellipse at 50% 35%, var(--bg-light) 0%, #b3aea6 55%, var(--bg-dark) 100%);
    position: relative;
    font-family: "Lato", sans-serif;
  }
  .brand-header {
    position: absolute;
    top: 116px; left: 0; width: 1200px;
    text-align: center;
    font-family: "Comfortaa", sans-serif;
    font-size: 32px;
    letter-spacing: 1px;
    color: #ffffff;
  }
  .soap-box {
    position: absolute;
    top: 300px;
    width: 288px; height: 412px;
    background: var(--box-white);
    box-shadow: 0 4px 10px rgba(0,0,0,0.25);
  }
  .soap-box--bergamot { left: 86px; --accent: var(--bergamot); --fruit: var(--bergamot-fruit); --soap: var(--soap-olive); --soap-hi: var(--soap-olive-light); }
  .soap-box--lemon { left: 446px; --accent: var(--lemon); --fruit: var(--lemon-fruit); --soap: var(--soap-olive); --soap-hi: var(--soap-olive-light); }
  .soap-box--duo { left: 806px; --accent: var(--grapefruit); --fruit: var(--grapefruit-fruit); --soap: var(--soap-peach); --soap-hi: var(--soap-peach-light); }

  .soap-window {
    position: absolute;
    left: 4px; top: 144px;
    width: 276px; height: 184px;
    background: linear-gradient(160deg, var(--soap-hi) 0%, var(--soap) 60%, var(--soap-hi) 100%);
  }
  .emblem { position: absolute; left: 0; top: 0; }
  .emblem-text {
    font-family: "Cinzel", serif;
    font-size: 8.5px;
    letter-spacing: 0.6px;
    fill: var(--ink);
  }
  .badge-text {
    font-family: "Cinzel", serif;
    font-size: 5px;
    letter-spacing: 0.3px;
    fill: var(--ink);
  }
  .box-brand {
    position: absolute;
    top: 56px; left: 0; width: 292px;
    text-align: center;
    font-family: "Comfortaa", sans-serif;
    font-size: 18px;
    letter-spacing: 0.5px;
    color: var(--ink);
  }
  .scent-band {
    position: absolute;
    left: 0; top: 360px;
    width: 288px; height: 23px;
    background: var(--accent);
    color: #ffffff;
    font-family: "Comfortaa", sans-serif;
    font-size: 17px;
    line-height: 23px;
    text-align: center;
    letter-spacing: 0.5px;
  }
  .net-weight {
    position: absolute;
    left: 0; top: 396px; width: 288px;
    text-align: center;
    font-size: 7.5px;
    color: var(--ink);
  }
</style>
</head>
<body>
  <div class="brand-header">Wrenfield</div>

  <div class="soap-box soap-box--bergamot">
    <div class="soap-window" role="img" aria-label="Cut-out window showing the olive bergamot soap bar"></div>
    <svg class="emblem" width="288" height="412" viewBox="0 0 288 412">
      <defs>
        <path id="arc-a" d="M 58 116 A 88 88 0 0 0 234 116"/>
        <path id="badge-top-a" d="M 204 120 A 21 21 0 0 1 246 120"/>
        <path id="badge-bot-a" d="M 204 120 A 21 21 0 0 0 246 120"/>
      </defs>
      <circle cx="146" cy="116" r="100" fill="#fff"/>
      <rect x="84" y="92" width="116" height="102" rx="40" fill="var(--fruit)" role="img" aria-label="Photo of bergamot fruit and leaves"/>
      <text class="emblem-text"><textPath href="#arc-a" startOffset="50%" text-anchor="middle">HANDCRAFTED ARTISAN NATURAL SOAP</textPath></text>
      <circle cx="225" cy="120" r="26" fill="#fff" stroke="#333" stroke-width="1"/>
      <circle cx="225" cy="120" r="14" fill="none" stroke="#333" stroke-width="1.2"/>
      <text class="badge-text"><textPath href="#badge-top-a" startOffset="50%" text-anchor="middle">NO SULFATES</textPath></text>
      <text class="badge-text" dy="4"><textPath href="#badge-bot-a" startOffset="50%" text-anchor="middle">NO PARABENS</textPath></text>
      <path d="M219 120 l5 6 l8 -12" fill="none" stroke="#222" stroke-width="2.4" stroke-linecap="round"/>
    </svg>
    <div class="box-brand">Wrenfield</div>
    <div class="scent-band">Bergamot</div>
    <div class="net-weight">4.5 oz (127.57 grams)</div>
  </div>

  <div class="soap-box soap-box--lemon">
    <div class="soap-window" role="img" aria-label="Cut-out window showing the olive lemon soap bar"></div>
    <svg class="emblem" width="288" height="412" viewBox="0 0 288 412">
      <defs>
        <path id="arc-b" d="M 58 116 A 88 88 0 0 0 234 116"/>
        <path id="badge-top-b" d="M 204 120 A 21 21 0 0 1 246 120"/>
        <path id="badge-bot-b" d="M 204 120 A 21 21 0 0 0 246 120"/>
      </defs>
      <circle cx="146" cy="116" r="100" fill="#fff"/>
      <rect x="88" y="86" width="112" height="108" rx="45" fill="var(--fruit)" role="img" aria-label="Photo of whole and halved lemons with leaves"/>
      <text class="emblem-text"><textPath href="#arc-b" startOffset="50%" text-anchor="middle">HANDCRAFTED ARTISAN NATURAL SOAP</textPath></text>
      <circle cx="225" cy="120" r="26" fill="#fff" stroke="#333" stroke-width="1"/>
      <circle cx="225" cy="120" r="14" fill="none" stroke="#333" stroke-width="1.2"/>
      <text class="badge-text"><textPath href="#badge-top-b" startOffset="50%" text-anchor="middle">NO SULFATES</textPath></text>
      <text class="badge-text" dy="4"><textPath href="#badge-bot-b" startOffset="50%" text-anchor="middle">NO PARABENS</textPath></text>
      <path d="M219 120 l5 6 l8 -12" fill="none" stroke="#222" stroke-width="2.4" stroke-linecap="round"/>
    </svg>
    <div class="box-brand">Wrenfield</div>
    <div class="scent-band">Lemon</div>
    <div class="net-weight">4.5 oz (127.57 grams)</div>
  </div>

  <div class="soap-box soap-box--duo">
    <div class="soap-window" role="img" aria-label="Cut-out window showing the speckled peach bergamot and grapefruit soap bar"></div>
    <svg class="emblem" width="288" height="412" viewBox="0 0 288 412">
      <defs>
        <path id="arc-c" d="M 58 116 A 88 88 0 0 0 234 116"/>
        <path id="badge-top-c" d="M 204 120 A 21 21 0 0 1 246 120"/>
        <path id="badge-bot-c" d="M 204 120 A 21 21 0 0 0 246 120"/>
      </defs>
      <circle cx="146" cy="116" r="100" fill="#fff"/>
      <rect x="84" y="84" width="116" height="100" rx="45" fill="var(--fruit)" role="img" aria-label="Photo of halved pink grapefruit and an orange"/>
      <text class="emblem-text"><textPath href="#arc-c" startOffset="50%" text-anchor="middle">HANDCRAFTED ARTISAN NATURAL SOAP</textPath></text>
      <circle cx="225" cy="120" r="26" fill="#fff" stroke="#333" stroke-width="1"/>
      <circle cx="225" cy="120" r="14" fill="none" stroke="#333" stroke-width="1.2"/>
      <text class="badge-text"><textPath href="#badge-top-c" startOffset="50%" text-anchor="middle">NO SULFATES</textPath></text>
      <text class="badge-text" dy="4"><textPath href="#badge-bot-c" startOffset="50%" text-anchor="middle">NO PARABENS</textPath></text>
      <path d="M219 120 l5 6 l8 -12" fill="none" stroke="#222" stroke-width="2.4" stroke-linecap="round"/>
    </svg>
    <div class="box-brand">Wrenfield</div>
    <div class="scent-band">Bergamot &amp; Grapefruit</div>
    <div class="net-weight">4.5 oz (127.57 grams)</div>
  </div>
</body>
</html>
```